Stonebridge Building and Projects business cards

A business card with watermark background (construction work)

Company logo attached

Home improvement projects
House renovations
Bathroom and kitchen renovations
House extensions
New builds and granny flats

Director Omar Haddani
(Phone number)
omar@sbpbuilding.com.au
(Instagram logo) sbp_building

```html
<!DOCTYPE html>
<html lang="en">
<head>
<meta charset="utf-8">
<title>Stonebridge Building and Projects – Business Cards</title>
<link href="https://fonts.googleapis.com/css2?family=Roboto:wght@400;500;700&display=swap" rel="stylesheet">
<style>
  :root {
    --page: #2b2b2d;
    --blue: #0b6dbd;
    --blue-deep: #075a9e;
    --band: #3d4045;
    --paper: #f3f4f6;
    --ink: #2f3338;
    --muted: #6c7178;
    --white: #ffffff;
  }
  * { margin: 0; padding: 0; box-sizing: border-box; }
  html, body { width: 1200px; height: 1050px; overflow: hidden; }
  body {
    background: var(--page);
    font-family: "Roboto", Arial, sans-serif;
    display: flex; flex-direction: column; align-items: center; justify-content: center;
    gap: 60px;
  }
  .card {
    position: relative; width: 700px; height: 400px; border-radius: 26px;
    overflow: hidden; box-shadow: 0 14px 30px rgba(0,0,0,.35);
  }

  /* Front */
  .card-front { background: linear-gradient(135deg, var(--blue) 0%, var(--blue-deep) 100%); color: var(--white); }
  .front-brand {
    position: absolute; top: 48px; left: 0; right: 0; text-align: center;
  }
  .brand-name {
    display: inline-flex; align-items: center; gap: 12px;
    font-weight: 700; font-size: 40px; line-height: 1.1; color: var(--white);
  }
  .brand-mark { width: 22px; height: 22px; background: var(--white); flex: none; }
  .brand-sub { display: block; font-weight: 700; font-size: 24px; color: var(--white); letter-spacing: 1px; }
  .tagline {
    display: inline-block; margin-top: 12px; font-size: 20px; font-weight: 500;
    border-bottom: 2px solid var(--white); padding-bottom: 2px;
  }
  .services {
    position: absolute; top: 238px; left: 0; right: 0; height: 84px;
    background: var(--band); display: flex; flex-direction: column; justify-content: center;
    align-items: center; font-size: 17px; line-height: 1.6;
  }
  .services .sep { margin: 0 8px; opacity: .8; }
  .front-links {
    position: absolute; top: 322px; bottom: 0; left: 0; right: 0;
    display: flex; justify-content: center; align-items: center; gap: 40px; font-size: 17px;
  }
  .link { display: inline-flex; align-items: center; gap: 9px; }
  .dot { width: 16px; height: 16px; border-radius: 50%; background: currentColor; flex: none; }

  /* Back */
  .card-back { background: var(--paper); }
  .construction-watermark {
    position: absolute; left: 0; top: 0; width: 440px; height: 400px;
    background: radial-gradient(ellipse at 40% 55%, rgba(180,186,194,.35), rgba(243,244,246,0) 70%);
  }
  .back-shape { position: absolute; inset: 0; }
  .back-brand {
    position: absolute; top: 70px; right: 34px; width: 250px; color: var(--white); text-align: center;
  }
  .back-brand .brand-name { font-size: 30px; gap: 10px; }
  .back-brand .brand-mark { width: 16px; height: 16px; }
  .back-brand .brand-sub { font-size: 18px; }
  .back-brand .tagline { font-size: 16px; margin-top: 10px; }
  .person { position: absolute; left: 56px; top: 150px; }
  .person-name { font-size: 30px; font-weight: 700; color: var(--blue); }
  .person-role { font-size: 18px; color: var(--muted); margin-top: 2px; }
  .contacts { list-style: none; margin-top: 22px; }
  .contacts li {
    display: flex; align-items: center; gap: 12px; font-size: 18px; color: var(--ink); height: 30px;
  }
  .contacts svg { width: 18px; height: 18px; flex: none; color: var(--blue); }
  .contacts .dot { color: var(--blue); }
</style>
</head>
<body>

<section class="card card-front" aria-label="Business card front">
  <div class="front-brand">
    <span class="brand-name"><span class="brand-mark"></span>Stonebridge</span>
    <span class="brand-sub">Building and Projects</span>
    <span class="tagline">Built right, every time!</span>
  </div>
  <div class="services">
    <p>Home Improvement Projects<span class="sep">|</span>House Renovations<span class="sep">|</span>House Extensions</p>
    <p>Bathroom &amp; Kitchen Renovations<span class="sep">|</span>New Builds &amp; Granny Flats</p>
  </div>
  <div class="front-links">
    <span class="link"><span class="dot"></span>sbp_building</span>
    <span class="link">
      <svg width="17" height="17" viewBox="0 0 24 24" fill="none" stroke="currentColor" stroke-width="2"><circle cx="12" cy="12" r="10"/><path d="M2 12h20M12 2c3 3 3 17 0 20M12 2c-3 3-3 17 0 20"/></svg>
      sbpbuilding.com.au
    </span>
  </div>
</section>

<section class="card card-back" aria-label="Business card back">
  <div class="construction-watermark" role="img" aria-label="Faint watermark of construction work"></div>
  <svg class="back-shape" viewBox="0 0 700 400" preserveAspectRatio="none" aria-hidden="true">
    <path d="M392 0 C440 170 540 315 700 362 L700 0 Z" fill="#3d4045"/>
    <path d="M378 0 C425 165 525 300 700 342 L700 0 Z" fill="#0b6dbd"/>
  </svg>
  <div class="back-brand">
    <span class="brand-name"><span class="brand-mark"></span>Stonebridge</span>
    <span class="brand-sub">Building and Projects</span>
    <span class="tagline">Built right, every time!</span>
  </div>
  <div class="person">
    <h1 class="person-name">Omar Haddani</h1>
    <p class="person-role">Managing Director</p>
    <ul class="contacts">
      <li><svg viewBox="0 0 24 24" fill="currentColor"><path d="M6.6 10.8a15 15 0 0 0 6.6 6.6l2.2-2.2c.3-.3.7-.4 1-.2 1.1.4 2.3.6 3.6.6.6 0 1 .4 1 1V20c0 .6-.4 1-1 1A17 17 0 0 1 3 4c0-.6.4-1 1-1h3.5c.6 0 1 .4 1 1 0 1.3.2 2.5.6 3.6.1.3 0 .7-.2 1z"/></svg>0400 318 274</li>
      <li><svg viewBox="0 0 24 24" fill="none" stroke="currentColor" stroke-width="2"><rect x="2" y="5" width="20" height="14" rx="2"/><path d="M2 6l10 7 10-7"/></svg>omar@sbpbuilding.com.au</li>
      <li><svg viewBox="0 0 24 24" fill="none" stroke="currentColor" stroke-width="2"><circle cx="12" cy="12" r="10"/><path d="M2 12h20M12 2c3 3 3 17 0 20M12 2c-3 3-3 17 0 20"/></svg>sbpbuilding.com.au</li>
      <li><span class="dot"></span>sbp_building</li>
    </ul>
  </div>
</section>

</body>
</html>
```